VELO MARANTA - LUXURY RESORT ZEPHYR HOTEL

We wanna promote the luxury hotel based on marroquian stylish luxury decor, it is still a project but we need to expose it.
Houses will be A frame type houses surrounded by florest and water dumps - please check - odeleite amber lynx at google to check localisation
Container luxury houses also will be included heaven blue velvet and green and rose gold are the Color. The sky is the limit.

```html
<!DOCTYPE html>
<html lang="en">
<head>
<meta charset="utf-8">
<title>Velo Maranta – Letterhead</title>
<link rel="stylesheet" href="https://fonts.googleapis.com/css2?family=Urbanist:wght@400;500;600;700&family=Cinzel:wght@400&display=swap">
<style>
  :root{
    --backdrop:#a9aaab;
    --paper:#ffffff;
    --gold:#b98a4e;
    --ink:#2b2b2b;
    --muted:#8c8a96;
    --band:#2f2b2c;
    --band-mid:#3f3a3c;
    --rule:#2a2627;
  }
  *{box-sizing:border-box;margin:0;padding:0}
  html,body{width:1200px;height:1041px;overflow:hidden}
  body{background:var(--backdrop);font-family:"Urbanist",sans-serif;color:var(--ink);position:relative}
  .letterhead{position:absolute;left:211px;top:20px;width:778px;height:1001px;background:var(--paper);overflow:hidden}

  .brand{position:absolute;left:15px;top:72px;font-weight:500;font-size:27px;letter-spacing:3px;color:var(--gold);line-height:1}
  .brand-rule{position:absolute;left:299px;top:84px;width:479px;height:12px}

  .recipient{position:absolute;left:37px;top:186px;font-size:14px;line-height:16px}
  .recipient .name{color:var(--gold);font-weight:700;letter-spacing:.3px}
  .recipient .role{font-weight:700}
  .recipient b{font-weight:700}
  .date{position:absolute;right:35px;top:226px;font-size:13.5px}
  .date b{color:var(--gold);font-weight:700}

  .body{position:absolute;left:37px;top:300px;width:704px;font-size:14px;line-height:18.6px;text-align:justify}
  .body p{margin-bottom:18.6px}
  .body .soft{color:var(--muted)}
  .body .firm{color:#333}

  .signature{position:absolute;left:560px;top:700px;width:160px;height:46px;background:linear-gradient(90deg,#eeeeee,#e2e2e2);border-radius:3px}
  .signer{position:absolute;left:540px;top:760px;width:200px;text-align:center}
  .signer .name{font-weight:700;font-size:15px;letter-spacing:.5px}
  .signer .title{font-size:9px;letter-spacing:1px;margin-top:6px}

  .contact{position:absolute;left:35px;display:flex;align-items:center;gap:12px;font-size:11px;line-height:15px}
  .contact.phone{top:866px}
  .contact.mail{top:906px}
  .contact b{font-weight:700;margin-right:4px}
  .icon-dot{width:24px;height:24px;border-radius:50%;background:var(--gold);display:flex;align-items:center;justify-content:center}

  .footer-band{position:absolute;left:0;top:941px;width:770px;height:36px}
  .footer-address{position:absolute;left:35px;top:941px;height:36px;display:flex;align-items:center;gap:12px;color:#fff;font-weight:700;font-size:11.5px;letter-spacing:1.4px}
  .footer-tag{position:absolute;left:398px;top:941px;height:36px;display:flex;align-items:center;color:#e8e4e0;font-family:"Cinzel",serif;font-size:12.5px;letter-spacing:1.6px}
</style>
</head>
<body>
  <main class="letterhead">
    <div class="brand">VELO MARANTA</div>
    <svg class="brand-rule" viewBox="0 0 479 12" aria-hidden="true">
      <rect x="0" y="0" width="155" height="12" fill="var(--rule)"/>
      <rect x="155" y="5" width="324" height="2" fill="var(--rule)"/>
    </svg>

    <div class="recipient">
      <div>To</div>
      <div class="name">Noel Varga</div>
      <div class="role">CEO, KELDORIA STUDIO</div>
      <div><b>W:</b> www.keldoriastudio.com</div>
    </div>
    <div class="date"><b>Date:</b> 24-03-2018</div>

    <section class="body">
      <p class="soft">Lorem ipsum dolor sit amet, consectetur adipiscing elit. Pellentesque dictum, ante non ullamcorp er convallis, nunc quam blandit metus, ac mollis eros felis a orci. Donec congue, mauris ut pulvinar lobortis, dolor massa feugiat nisi, at tincidunt metus leo vel elit. Proin facilisis semper lobortis. Vivamus augue purus, cursus quis urna non, accumsan pellentesque est. Nulla in iaculis magna, quis aliqu et ex. Cras efficitur metus eget purus euismod facilisis. Proin non metus tincidunt, auctor ipsum a, tempor mi.</p>
      <p class="firm">Nulla egestas vulputate risus, ut vestibulum diam commodo id. Mauris ornare libero eu erat portt itor ultrices. Proin sed lectus scelerisque ligula bibendum sagittis ac nec leo. Donec ac accumsan diam, et lobortis mauris.</p>
      <p class="firm">Nulla congue volutpat nisl ac lobortis. Integer dignissim interdum libero, quis feugiat velit pretium at. Phasellus sit amet libero rutrum, feugiat odio et, tempus purus. Cras ultricies, leo at fringilla solli cit udin, leo sapien placerat enim, a rutrum lorem enim ut tortor. Phasellus magna ante, cong ue maximus egestas sit amet, venenatis scelerisque felis.</p>
      <p class="soft">Nulla congue volutpat nisl ac lobortis. Integer dignissim interdum libero, quis feugiat velit pretium at. Phasellus sit amet libero rutrum, feugiat odio et, tempus purus. Cras ultricies, leo at fringilla solli cit udin, leo sapien placerat enim, a rutrum lorem enim ut tortor. Phasellus magna ante, cong ue maximus egestas sit amet, venenatis scelerisque felis.</p>
    </section>

    <div class="signature" role="img" aria-label="Handwritten signature of Seren Okafor"></div>
    <div class="signer">
      <div class="name">[ SEREN OKAFOR ]</div>
      <div class="title">FOUNDER</div>
    </div>

    <div class="contact phone">
      <span class="icon-dot">
        <svg width="12" height="12" viewBox="0 0 24 24" aria-hidden="true"><path fill="#fff" d="M6.6 10.8a15.1 15.1 0 0 0 6.6 6.6l2.2-2.2c.3-.3.7-.4 1-.2 1.1.4 2.3.6 3.6.6.6 0 1 .4 1 1V20c0 .6-.4 1-1 1A17 17 0 0 1 3 4c0-.6.4-1 1-1h3.5c.6 0 1 .4 1 1 0 1.3.2 2.5.6 3.6.1.3 0 .7-.2 1z"/></svg>
      </span>
      <div><div><b>T:</b>+00 1X XXXX XXXX</div><div><b>F:</b>+00 1X XXXX XXXX</div></div>
    </div>
    <div class="contact mail">
      <span class="icon-dot">
        <svg width="12" height="12" viewBox="0 0 24 24" aria-hidden="true"><rect x="3" y="5" width="18" height="14" rx="2" fill="none" stroke="#fff" stroke-width="2"/><path d="M3 7l9 6 9-6" fill="none" stroke="#fff" stroke-width="2"/></svg>
      </span>
      <div><div><b>E:</b>Seren.Okafor@velomaranta.com</div><div><b>W:</b>www.velomaranta.com</div></div>
    </div>

    <svg class="footer-band" viewBox="0 0 770 36" aria-hidden="true">
      <rect width="770" height="36" fill="var(--band)"/>
      <polygon points="366,0 682,0 694,18 682,36 366,36 378,18" fill="var(--band-mid)"/>
      <polyline points="366,0 378,18 366,36" fill="none" stroke="#fff" stroke-width="2"/>
      <polyline points="682,0 694,18 682,36" fill="none" stroke="#fff" stroke-width="2"/>
    </svg>
    <div class="footer-address">
      <span class="icon-dot">
        <svg width="12" height="12" viewBox="0 0 24 24" aria-hidden="true"><circle cx="12" cy="12" r="9" fill="none" stroke="#fff" stroke-width="2"/><path d="M3 12h18M12 3c3 3 3 15 0 18M12 3c-3 3-3 15 0 18" fill="none" stroke="#fff" stroke-width="1.6"/></svg>
      </span>
      <span>ORVELL QUAY – PORTMERE</span>
    </div>
    <div class="footer-tag">LUXURY RESORT ZEPHYR HOTEL</div>
  </main>
</body>
</html>
```